full stationary design for a modern sleek design company

we are a design company that does modern minimalistic interior design works as well as other design services for high end clients.
we need a full stationary design including and not limited to (double sided business card, letter head, envelopes, documents folder...etc) that reflects the modern style design we do.
sleek modern and minimalistic is the requirements.
Updates

please use the latest attached files as there was a slight modification on the logo Added Wednesday, March 1, 2017

minor update on the logo files in JPG and PSD has been updated kindly follow the new attachments. Added Thursday, March 2, 2017

Target Market(s)

modern minimalist clients

Industry/Entity Type

Design Agency

Requirements
Must have
• the logo
Nice to have
• i like the colors in the colored 3D logo attached
Should not have
• too many colors

```html
<!DOCTYPE html>
<html lang="en">
<head>
<meta charset="utf-8">
<title>Linea Atelier – Business Card</title>
<link rel="stylesheet" href="https://fonts.googleapis.com/css2?family=Open+Sans:wght@400;600;700&display=swap">
<style>
  :root {
    --backdrop: #7a5538;
    --card-white: #ffffff;
    --brand-orange: #f7941d;
    --ink-dark: #3a3d42;
    --ink-text: #4a4a4a;
    --rule-grey: #d9d9d9;
  }
  * { margin: 0; padding: 0; box-sizing: border-box; }
  html, body {
    width: 1200px;
    height: 987px;
    overflow: hidden;
  }
  body {
    background: var(--backdrop);
    font-family: "Open Sans", Arial, sans-serif;
    position: relative;
  }
  .card {
    position: absolute;
    left: 292px;
    width: 616px;
  }

  /* Front side */
  .card-front {
    top: 130px;
    height: 352px;
    background: var(--card-white);
  }
  .card-front .accent-line {
    position: absolute;
    left: 0; right: 0;
    top: 327px;
    height: 3px;
    background: var(--brand-orange);
  }
  .card-front .base-band {
    position: absolute;
    left: 0; right: 0;
    top: 333px;
    height: 19px;
    background: var(--ink-dark);
  }
  .brand {
    position: absolute;
    display: flex;
    align-items: center;
    gap: 10px;
    font-weight: 700;
    letter-spacing: 2px;
    text-transform: uppercase;
    white-space: nowrap;
  }
  .brand-mark {
    display: block;
    flex: none;
  }
  .card-front .brand {
    left: 50px;
    top: 152px;
    font-size: 23px;
    color: var(--ink-dark);
  }
  .card-front .brand-mark {
    width: 22px; height: 22px;
    background: var(--brand-orange);
  }
  .divider {
    position: absolute;
    left: 335px;
    top: 72px;
    width: 1px;
    height: 188px;
    background: var(--rule-grey);
  }
  .contact {
    position: absolute;
    left: 359px;
    top: 68px;
    color: var(--ink-text);
  }
  .contact .person-name {
    font-size: 23px;
    font-weight: 600;
    color: var(--brand-orange);
    line-height: 30px;
    text-transform: uppercase;
  }
  .contact .person-role {
    font-size: 17px;
    line-height: 22px;
    color: #333;
    margin-bottom: 12px;
  }
  .contact address {
    font-style: normal;
    font-size: 16px;
    line-height: 22px;
    margin-bottom: 6px;
  }
  .contact-list { list-style: none; }
  .contact-list li {
    display: flex;
    align-items: center;
    gap: 8px;
    font-size: 16px;
    line-height: 23.5px;
  }
  .contact-list svg {
    width: 14px; height: 14px;
    flex: none;
    fill: var(--brand-orange);
  }

  /* Back side */
  .card-back {
    top: 505px;
    height: 352px;
    background: var(--brand-orange);
  }
  .card-back .brand {
    left: 0; right: 0;
    top: 156px;
    justify-content: center;
    font-size: 36px;
    color: var(--card-white);
  }
  .card-back .brand-mark {
    width: 32px; height: 32px;
    background: var(--card-white);
  }
</style>
</head>
<body>

  <section class="card card-front" aria-label="Business card front">
    <div class="brand">
      <span class="brand-mark"></span>
      <span class="brand-name">Linea Atelier</span>
    </div>
    <div class="divider"></div>
    <div class="contact">
      <p class="person-name">Adam Rowe</p>
      <p class="person-role">CEO&amp;Founder</p>
      <address>1420 Birchwood Road<br>Fairview, Oregon 97024</address>
      <ul class="contact-list">
        <li>
          <svg viewBox="0 0 16 16" aria-hidden="true"><path d="M3.6 1.2 6 3.6c.4.4.4 1 0 1.4L4.8 6.2a9 9 0 0 0 5 5l1.2-1.2c.4-.4 1-.4 1.4 0l2.4 2.4c.4.4.4 1 0 1.4l-1.3 1.3C11.9 16.7 0 4.8 1.9 3.2L2.2 1.2c.4-.4 1-.4 1.4 0z"/></svg>
          (555) 214 3890
        </li>
        <li>
          <svg viewBox="0 0 16 16" aria-hidden="true"><path d="M4.5 0h7A1.5 1.5 0 0 1 13 1.5v13a1.5 1.5 0 0 1-1.5 1.5h-7A1.5 1.5 0 0 1 3 14.5v-13A1.5 1.5 0 0 1 4.5 0zM5 2v10h6V2zm3 11a1 1 0 1 0 0 2 1 1 0 0 0 0-2z"/></svg>
          (555) 730 6127
        </li>
        <li>
          <svg viewBox="0 0 16 16" aria-hidden="true"><path d="M1 3h14v1.2L8 8.6 1 4.2zm0 2.6 7 4.4 7-4.4V13H1z"/></svg>
          adam@lineaatelier.com
        </li>
        <li>
          <svg viewBox="0 0 16 16" aria-hidden="true"><path d="M8 0a8 8 0 1 0 0 16A8 8 0 0 0 8 0zm0 1.6c.9 0 1.9 1.6 2.3 4.1H5.7C6.1 3.2 7.1 1.6 8 1.6zM5.5 7.3h5a14 14 0 0 1 0 1.4h-5a14 14 0 0 1 0-1.4zM8 14.4c-.9 0-1.9-1.6-2.3-4.1h4.6c-.4 2.5-1.4 4.1-2.3 4.1z"/></svg>
          www.lineaatelier.com
        </li>
      </ul>
    </div>
    <div class="accent-line"></div>
    <div class="base-band"></div>
  </section>

  <section class="card card-back" aria-label="Business card back">
    <div class="brand">
      <span class="brand-mark"></span>
      <span class="brand-name">Linea Atelier</span>
    </div>
  </section>

</body>
</html>
```